BRIGHT RIVER POWER.

I'd like my business logo.
contact name: Dennis Halvorsen
phone:0438759164
email: info@brightriverpower.net.au
website: www.brightriverpower.net.au

services:
solar
battery storage
LED lighting
energy saving solutions
general electrical
I'd like the design to look professional

Target Market(s)

Everyone

Industry/Entity Type

Business

Contact Information for Business Card

as described above

Requirements
Must have
• Id like the colours and the design to work well with my logo.

```html
<!DOCTYPE html>
<html lang="en">
<head>
<meta charset="utf-8">
<title>Bright River Power – Business Card</title>
<link rel="stylesheet" href="https://fonts.googleapis.com/css2?family=Ubuntu:wght@400;500;700&display=swap">
<style>
  :root {
    --page-bg: #e9e7e2;
    --card-black: #0a0a0a;
    --card-black-soft: #1c1c1c;
    --green: #2ea64f;
    --green-light: #72c444;
    --orange: #f39a1e;
    --white: #f4f4f4;
    --grey: #d8d8d8;
  }
  html, body {
    margin: 0;
    width: 1200px;
    height: 1022px;
    overflow: hidden;
    background: var(--page-bg);
    font-family: "Ubuntu", Arial, sans-serif;
  }
  .card {
    position: absolute;
    left: 100px;
    top: 225px;
    width: 1000px;
    height: 572px;
    border-radius: 18px;
    overflow: hidden;
    background: linear-gradient(160deg, var(--card-black-soft) 0%, var(--card-black) 55%);
    box-shadow: 0 18px 40px rgba(0,0,0,.25);
  }
  .card-shapes { position: absolute; inset: 0; }
  .brand {
    position: absolute;
    left: 60px;
    top: 190px;
    display: flex;
    align-items: center;
    gap: 18px;
  }
  .brand-dot {
    width: 62px; height: 62px; border-radius: 50%;
    background: var(--orange);
  }
  .brand-name {
    font-weight: 700;
    font-size: 38px;
    line-height: 1.05;
    color: var(--green-light);
    width: 260px;
  }
  .services {
    position: absolute;
    left: 330px;
    top: 318px;
    margin: 0; padding: 0;
    list-style: none;
    color: var(--white);
    font-size: 25px;
    line-height: 37px;
  }
  .services li::before {
    content: "";
    display: inline-block;
    width: 10px; height: 10px; border-radius: 50%;
    background: var(--orange);
    margin-right: 16px;
    vertical-align: middle;
  }
  .contact-name {
    position: absolute;
    right: 92px;
    top: 214px;
    color: var(--orange);
    font-weight: 500;
    font-size: 32px;
  }
  .contact-list {
    position: absolute;
    right: 50px;
    top: 306px;
    margin: 0; padding: 0;
    list-style: none;
    color: var(--white);
    font-size: 23px;
    line-height: 40px;
    text-align: right;
  }
  .contact-list li { display: flex; justify-content: flex-end; align-items: center; gap: 14px; }
  .contact-list svg { width: 20px; height: 20px; }
  .web-highlight { color: var(--orange); }
</style>
</head>
<body>
  <div class="card">
    <svg class="card-shapes" viewBox="0 0 1000 572" width="1000" height="572" aria-hidden="true">
      <rect class="corner-tab" x="880" y="0" width="70" height="34" fill="var(--green)"/>
      <line class="divider" x1="300" y1="282" x2="955" y2="282" stroke="var(--white)" stroke-width="3"/>
      <polygon class="green-band" points="280,550 640,550 700,455 1000,455 1000,572 280,572" fill="var(--green)"/>
      <polygon class="green-edge" points="280,540 636,540 696,445 1000,445 1000,455 700,455 640,550 280,550" fill="var(--green-light)"/>
    </svg>

    <div class="brand">
      <span class="brand-dot"></span>
      <span class="brand-name">BRIGHT RIVER POWER</span>
    </div>

    <ul class="services">
      <li>Solar</li>
      <li>Battery storage</li>
      <li>LED lighting</li>
      <li>Energy saving solutions</li>
    </ul>

    <div class="contact-name">Dennis Halvorsen</div>

    <ul class="contact-list">
      <li>0438759164
        <svg viewBox="0 0 20 20"><path d="M5 2l3 4-2 2c1 2 3 4 5 5l2-2 4 3-2 3C9 17 3 11 2 5z" fill="none" stroke="var(--orange)" stroke-width="1.6"/></svg>
      </li>
      <li>info@brightriverpower.net.au
        <svg viewBox="0 0 20 20"><rect x="2" y="4" width="16" height="12" fill="none" stroke="var(--orange)" stroke-width="1.6"/><path d="M2 4l8 7 8-7" fill="none" stroke="var(--orange)" stroke-width="1.6"/></svg>
      </li>
      <li><span>www.<span class="web-highlight">brightriverpower</span>.net.au</span>
        <svg viewBox="0 0 20 20"><circle cx="10" cy="10" r="8" fill="none" stroke="var(--orange)" stroke-width="1.6"/><ellipse cx="10" cy="10" rx="3.5" ry="8" fill="none" stroke="var(--orange)" stroke-width="1.4"/><line x1="2" y1="10" x2="18" y2="10" stroke="var(--orange)" stroke-width="1.4"/></svg>
      </li>
    </ul>
  </div>
</body>
</html>
```